Product Packaging design for Vaporizer Battery box

We are looking for product packaging for a new line of Vaporizer Batteries. These batteries are all sold in bundle packs, and each battery has its own cardboard box. For example, the bundle packs are simply bagged up packs of 2, 3, 5, 10, 25, etc.

There are 4 different kinds of batteries that we need the packaging designed for. I have attached templates of the packaging for your reference. I would like the packaging to be a similar theme across all the batteries to keep things consistent.

More details about the 4 batteries can be found on our website at:
http://www.tidemarkgoodsdepot.example/product-category/vape_batteries/
Password: tidevisit

Packing Requirements

The packaging should have our company logo somewhere on it. I have attached a few different variations/orientations of our logo for you to choose between.

The name of the battery
Tidemark Goods 1300mAh Variable Voltage Large Capacity Battery
Tidemark Goods 400mAh Slim Variable Voltage Battery
Tidemark Goods 280mAh Slim Automatic Buttonless Battery
Tidemark Goods 350mAh KOV Slim Battery

Company website www.TidemarkGoodsDepot.example

For the Tidemark Goods 350mAh KOV Slim Battery, have the product packaging color scheme be Black base with Gold wording/trim. This battery only comes in black and gold, so the packaging will match.

Make sure to use the proper packaging template for the batteries. There are only two templates and pretty much the only difference is the size. They both fold up to be a rectangle package.

Industry/Entity Type

Product

Colors

Designer to choose colors to be used in the design.

Requirements
Must have
• Packing Requirements
• The packaging should have our company logo somewhere on it. I have attached a few different variations/orientations of our logo for you to choose between.
• The name of the battery
• Tidemark Goods 1300mAh Variable Voltage Large Capacity Battery
• Tidemark Goods 400mAh Slim Variable Voltage Battery
• Tidemark Goods 280mAh Slim Automatic Buttonless Battery
• Tidemark Goods 350mAh KOV Slim Battery
• Company website www.TidemarkGoodsDepot.example
• For the Tidemark Goods 350mAh KOV Slim Battery, have the product packaging color scheme be Black base with Gold wording/trim. This battery only comes in black and gold, so the packaging will match.
• Make sure to use the proper packaging template for the batteries. There are only two templates and pretty much the only difference is the size. They both fold up to be a rectangle package.

```html
<!DOCTYPE html>
<html lang="en">
<head>
<meta charset="utf-8">
<title>Tidemark Goods 1300mAh Battery Packaging</title>
<link rel="stylesheet" href="https://fonts.googleapis.com/css2?family=Arimo:wght@400;700&display=swap">
<style>
  :root {
    --box-black: #1e1c1d;
    --trim-white: #ffffff;
    --accent-yellow: #f7d337;
    --accent-rust: #b8461f;
    --accent-green: #8cc43f;
    --spec-dark: #2a2526;
    --spec-light: #fbe9e0;
    --stage-top: #dadada;
    --stage-bottom: #ffffff;
  }
  * { box-sizing: border-box; margin: 0; padding: 0; }
  html, body { width: 1022px; height: 1200px; overflow: hidden; }
  body {
    position: relative;
    background: linear-gradient(to bottom, var(--stage-top) 0%, var(--stage-bottom) 70%);
    font-family: "Arimo", Arial, sans-serif;
  }
  .box-front {
    position: absolute;
    width: 132px;
    height: 730px;
    background: var(--box-black);
    overflow: hidden;
  }
  .box-front--yellow { left: 228px; top: 195px; --accent: var(--accent-yellow); --spec: var(--spec-dark); }
  .box-front--rust   { left: 425px; top: 255px; --accent: var(--accent-rust);   --spec: var(--spec-light); }
  .box-front--green  { left: 620px; top: 180px; --accent: var(--accent-green);  --spec: var(--spec-dark); }

  .box-front__trim { position: absolute; inset: 0; width: 100%; height: 100%; }
  .trim-stripe { fill: var(--trim-white); }
  .trim-field { fill: var(--accent); }

  .brand-mark {
    position: absolute;
    top: 110px;
    left: 50%;
    width: 24px;
    height: 24px;
    margin-left: -12px;
    background: var(--accent);
  }
  .brand-name {
    position: absolute;
    top: 150px;
    left: 50%;
    transform: translateX(-50%);
    writing-mode: vertical-rl;
    font-weight: 700;
    font-size: 30px;
    letter-spacing: 2px;
    color: var(--trim-white);
    white-space: nowrap;
  }
  .spec {
    position: absolute;
    left: 14px;
    bottom: 26px;
    color: var(--spec);
  }
  .spec__capacity {
    font-weight: 700;
    font-size: 16px;
    line-height: 1.2;
  }
  .spec__line {
    font-weight: 400;
    font-size: 10.5px;
    line-height: 1.25;
  }
</style>
</head>
<body>

  <section class="box-front box-front--yellow">
    <svg class="box-front__trim" viewBox="0 0 132 730" preserveAspectRatio="none">
      <polygon class="trim-stripe" points="0,568 132,422 132,458 0,576"/>
      <polygon class="trim-field" role="img" aria-label="Yellow diamond lattice pattern" points="0,576 132,458 132,730 0,730"/>
    </svg>
    <span class="brand-mark"></span>
    <h1 class="brand-name">TIDEMARK GOODS</h1>
    <div class="spec">
      <p class="spec__capacity">1300mAh</p>
      <p class="spec__line">Variable Voltage</p>
      <p class="spec__line">Large Capacity</p>
      <p class="spec__line">Battery</p>
    </div>
  </section>

  <section class="box-front box-front--rust">
    <svg class="box-front__trim" viewBox="0 0 132 730" preserveAspectRatio="none">
      <polygon class="trim-stripe" points="0,568 132,422 132,458 0,576"/>
      <polygon class="trim-field" role="img" aria-label="Rust diamond lattice pattern" points="0,576 132,458 132,730 0,730"/>
    </svg>
    <span class="brand-mark"></span>
    <h1 class="brand-name">TIDEMARK GOODS</h1>
    <div class="spec">
      <p class="spec__capacity">1300mAh</p>
      <p class="spec__line">Variable Voltage</p>
      <p class="spec__line">Large Capacity</p>
      <p class="spec__line">Battery</p>
    </div>
  </section>

  <section class="box-front box-front--green">
    <svg class="box-front__trim" viewBox="0 0 132 730" preserveAspectRatio="none">
      <polygon class="trim-stripe" points="0,568 132,422 132,458 0,576"/>
      <polygon class="trim-field" role="img" aria-label="Green diamond lattice pattern" points="0,576 132,458 132,730 0,730"/>
    </svg>
    <span class="brand-mark"></span>
    <h1 class="brand-name">TIDEMARK GOODS</h1>
    <div class="spec">
      <p class="spec__capacity">1300mAh</p>
      <p class="spec__line">Variable Voltage</p>
      <p class="spec__line">Large Capacity</p>
      <p class="spec__line">Battery</p>
    </div>
  </section>

</body>
</html>
```